Website redesign www.marigoldlawpc.com law firm site

Need to redesign the website that I currently have to look more modern and professional. Would also like to be able to make updates and post without having a huge hassle. See current www.marigoldlawpc.com. I just think that it looks very immature and it's very templated there's no ability for me to make posts or Add links or anything like that

Target Market(s)

California people looking for a powerhouse attorney in

Industry/Entity Type

Legal

Number of Pages Required

3 page

Font styles to use
Serif
Sans Serif

Colors
ec1f27
000000
ffffff

Requirements
Must have
• Must be mobile friendly. Must look professional and have ability to post links to other websites. Must have ability to post blogs or articles. Would like to be able to read my FeeTrove account and also have the ability to upload forms for people to download
Nice to have
• Simple design easy to use and not cluttered with too much text

```html
<!DOCTYPE html>
<html lang="en">
<head>
<meta charset="utf-8">
<title>Marigold Law P.C</title>
<link rel="stylesheet" href="https://fonts.googleapis.com/css2?family=Cinzel:wght@400;700&family=Open+Sans:wght@400;600;700&display=swap">
<style>
:root{
  --red:#ec1f27;
  --red-dark:#a3141a;
  --black:#000000;
  --ink:#222222;
  --grey-text:#8a8a8a;
  --nav:#333333;
  --band:#efefef;
  --white:#ffffff;
}
*{margin:0;padding:0;box-sizing:border-box}
html,body{width:1200px;height:2965px;overflow:hidden;background:var(--white)}
body{position:relative;font-family:"Open Sans",Arial,sans-serif;color:var(--ink)}
.abs{position:absolute}
.serif{font-family:"Cinzel",Georgia,serif}

/* header */
.site-header{left:0;top:0;width:1200px;height:123px}
.brand{left:79px;top:18px;font-family:"Cinzel",Georgia,serif;font-weight:400;color:var(--red);font-size:44px;line-height:1.1}
.brand small{display:block;font-size:22px;text-align:center;width:310px}
.call{left:826px;top:30px;display:flex;align-items:center;gap:16px}
.call-icon{width:60px;height:60px;border:2px solid var(--red);border-radius:50%;display:flex;align-items:center;justify-content:center}
.call-label{font-size:17px;color:var(--ink);line-height:1.2}
.call-number{font-size:31px;font-weight:700;color:var(--red);line-height:1.15}

/* nav */
.main-nav{left:0;top:123px;width:1200px;height:55px;background:var(--nav);display:flex;padding-left:77px}
.main-nav a{color:var(--white);text-decoration:none;font-size:18px;height:55px;line-height:55px;padding:0 33px}
.main-nav a.active{background:var(--red);padding:0 34px 0 34px;margin-right:0}

/* hero */
.hero{left:0;top:178px;width:1200px;height:575px;background:linear-gradient(180deg,#c8d6e6 0%,#e8eef3 35%,#b9b9b4 60%,#6f6e6a 100%)}
.hero-title{left:0;top:140px;width:1200px;text-align:center;font-weight:700;font-size:39px;line-height:63px;color:#151515;letter-spacing:-0.5px}
.btn-red{background:var(--red);color:var(--white);text-decoration:none;display:flex;align-items:center;justify-content:center}
.hero .btn-red{left:504px;top:277px;width:192px;height:61px;font-size:22px;font-weight:600}

/* practice */
.practice{left:0;top:753px;width:1200px;height:417px;background:var(--band)}
.section-title{font-family:"Cinzel",Georgia,serif;font-size:44px;font-weight:400;color:var(--ink);text-align:center;width:1200px;left:0;letter-spacing:1px}
.section-title span{color:var(--red)}
.practice .section-title{top:30px}
.area{width:255px;display:flex;gap:16px}
.area-icon{width:58px;height:58px;background:var(--white);flex:none;display:flex;align-items:center;justify-content:center}
.area h3{font-size:19px;font-weight:400;color:var(--ink);line-height:1.2;margin-top:-2px}
.area p{font-size:14px;color:var(--grey-text);line-height:23px;margin-top:2px}

/* welcome */
.portrait{left:95px;top:1218px;width:225px;height:245px;border:4px solid #dcdcdc;background:linear-gradient(160deg,#5a3f2c,#c99b7f 55%,#7a5a46)}
.welcome-title{left:411px;top:1223px;font-family:"Cinzel",Georgia,serif;font-size:44px;color:var(--ink);letter-spacing:1px}
.welcome-title span{color:var(--red)}
.welcome-text{left:409px;top:1295px;width:705px;font-size:15px;line-height:25px;color:#555}
.welcome .btn-red{left:409px;top:1386px;width:166px;height:49px;font-family:"Cinzel",Georgia,serif;font-size:19px;border-radius:3px}

/* testimonials */
.reviews{left:0;top:1540px;width:1200px;height:417px;background:radial-gradient(ellipse at 70% 40%,#4a3a2a 0%,#221a13 55%,#120e0b 100%)}
.reviews .section-title{top:40px;color:var(--white)}
.quote-mark{left:0;top:112px;width:1200px;text-align:center}
.review-text{left:150px;top:153px;width:900px;text-align:center;font-size:16px;line-height:26px;color:var(--white)}
.review-tag{left:459px;top:231px;width:282px;height:50px;border:2px solid #d8d8d8;color:var(--white);font-size:22px;display:flex;align-items:center;justify-content:center}
.review-author{left:0;top:306px;width:1200px;text-align:center;font-size:15px;color:var(--white)}
.dots{left:558px;top:348px;display:flex;gap:13px}
.dots i{width:18px;height:18px;border-radius:50%;background:var(--white);display:block}
.dots i.on{background:var(--red)}

/* news */
.news-title{top:2015px}
.post{width:235px;top:2080px}
.post-image{height:142px}
.post h4{font-size:17px;font-weight:400;color:var(--red);line-height:25px;margin-top:20px}
.post time{display:block;font-size:14px;color:var(--grey-text);margin-top:6px}
.post p{font-size:14px;color:var(--grey-text);line-height:25px;margin-top:4px}

/* ratings */
.ratings{left:77px;top:2459px;width:1046px;height:145px;background:var(--band)}
.ratings-label{left:0;top:0;width:293px;height:145px;background:var(--red);color:var(--white);font-family:"Cinzel",Georgia,serif;font-size:38px;line-height:55px;padding:20px 0 0 24px}
.badge{background:#cfcfcf}

/* footer */
.footer{left:0;top:2683px;width:1200px;height:231px;background:var(--red);color:var(--white)}
.footer-nav{left:79px;top:34px;display:flex;gap:29px;font-size:15px}
.footer-nav a{color:var(--white);text-decoration:none}
.social{left:940px;top:20px;display:flex;gap:21px}
.social i{width:46px;height:46px;border-radius:50%;background:var(--black);display:block}
.social i+i{background:var(--white);border:2px solid #222}
.contact-item{display:flex;gap:14px;align-items:flex-start;font-size:15px;line-height:25px;top:134px}
.contact-icon{width:48px;height:48px;border-radius:50%;background:var(--white);flex:none;display:flex;align-items:center;justify-content:center}
.contact-item a{color:var(--white)}
.legal{left:0;top:2914px;width:1200px;height:51px;background:var(--red-dark);color:var(--white);font-size:15px;text-align:center;line-height:51px}
</style>
</head>
<body>

<header class="abs site-header">
  <div class="abs brand">Marigold Law<small>P.C</small></div>
  <div class="abs call">
    <span class="call-icon">
      <svg width="26" height="26" viewBox="0 0 24 24"><path fill="#ec1f27" d="M6.6 10.8a15.2 15.2 0 0 0 6.6 6.6l2.2-2.2c.3-.3.7-.4 1-.2 1.1.4 2.3.6 3.6.6.6 0 1 .4 1 1V20c0 .6-.4 1-1 1A17 17 0 0 1 3 4c0-.6.4-1 1-1h3.5c.6 0 1 .4 1 1 0 1.3.2 2.5.6 3.6.1.3 0 .7-.2 1z"/></svg>
    </span>
    <div><div class="call-label">CALL US NOW!</div><div class="call-number">(555) 014-2870</div></div>
  </div>
</header>

<nav class="abs main-nav">
  <a class="active" href="#">HOME</a><a href="#">OUR ATTORNEY</a><a href="#">PRACTICE AREAS</a><a href="#">CLIENT REVIEWS</a><a href="#">LINKS</a><a href="#">CONTACT</a>
</nav>

<section class="abs hero" role="img" aria-label="Sunlit city skyline with skyscrapers">
  <h1 class="abs hero-title">WE ARE DEDICATED &amp;<br>EXPERIENCED TRIAL ATTORNEYS.</h1>
  <a class="abs btn-red" href="#">CONTACT US</a>
</section>

<section class="abs practice">
  <h2 class="abs section-title">Our Practice <span>Areas</span></h2>

  <div class="abs area" style="left:77px;top:123px">
    <span class="area-icon"><svg width="34" height="34" viewBox="0 0 24 24"><rect x="3" y="8" width="18" height="12" fill="#ec1f27"/><rect x="9" y="4" width="6" height="4" fill="none" stroke="#ec1f27" stroke-width="2"/></svg></span>
    <div><h3>Business Law</h3><p>Small and medium sized businesses have many of the same legal issues</p></div>
  </div>
  <div class="abs area" style="left:348px;top:123px">
    <span class="area-icon"><svg width="34" height="34" viewBox="0 0 24 24"><rect x="3" y="6" width="7" height="15" fill="#ec1f27"/><rect x="12" y="3" width="9" height="18" fill="#ec1f27"/></svg></span>
    <div><h3>Real Estate Law</h3><p>At Marigold Law P.C., we help Californians who need legal advice</p></div>
  </div>
  <div class="abs area" style="left:619px;top:123px">
    <span class="area-icon"><svg width="34" height="34" viewBox="0 0 24 24"><rect x="3" y="6" width="4" height="15" fill="#ec1f27"/><rect x="9" y="10" width="4" height="11" fill="#ec1f27"/><rect x="15" y="14" width="4" height="7" fill="#ec1f27"/><path d="M4 3l16 12" stroke="#ec1f27" stroke-width="2"/></svg></span>
    <div><h3>Bankruptcy</h3><p>If your finances are dwindling to the point where you</p></div>
  </div>
  <div class="abs area" style="left:888px;top:123px">
    <span class="area-icon"><svg width="34" height="34" viewBox="0 0 24 24"><circle cx="7" cy="5" r="2.5" fill="#ec1f27"/><circle cx="17" cy="5" r="2.5" fill="#ec1f27"/><circle cx="12" cy="11" r="2" fill="#ec1f27"/><rect x="4.5" y="9" width="5" height="12" fill="#ec1f27"/><rect x="14.5" y="9" width="5" height="12" fill="#ec1f27"/><rect x="10.5" y="14" width="3" height="7" fill="#ec1f27"/></svg></span>
    <div><h3>Family Law</h3><p>Family Law is one area of legal concern that brings many people</p></div>
  </div>
  <div class="abs area" style="left:77px;top:259px">
    <span class="area-icon"><svg width="34" height="34" viewBox="0 0 24 24"><circle cx="7" cy="14" r="5" fill="none" stroke="#ec1f27" stroke-width="2"/><circle cx="17" cy="14" r="5" fill="none" stroke="#ec1f27" stroke-width="2"/><path d="M10 10l4-5" stroke="#ec1f27" stroke-width="2"/></svg></span>
    <div><h3>Criminal Law</h3><p>Riverton Criminal Law Attorney If you were charged with a criminal</p></div>
  </div>
  <div class="abs area" style="left:348px;top:259px">
    <span class="area-icon"><svg width="34" height="34" viewBox="0 0 24 24"><rect x="3" y="18" width="12" height="3" fill="#ec1f27"/><rect x="9" y="3" width="6" height="9" transform="rotate(-45 12 7.5)" fill="#ec1f27"/><path d="M14 11l7 7" stroke="#ec1f27" stroke-width="2.5"/></svg></span>
    <div><h3>Civil Litigation</h3><p>Civil litigation is a vast legal category than can include everything</p></div>
  </div>
  <div class="abs area" style="left:619px;top:259px">
    <span class="area-icon"><svg width="34" height="34" viewBox="0 0 24 24"><path d="M5 2h10l4 4v16H5z" fill="none" stroke="#ec1f27" stroke-width="2"/><path d="M8 10h8M8 14h8M8 18h6" stroke="#ec1f27" stroke-width="2"/></svg></span>
    <div><h3>Unlawful Detainer</h3><p>Riverton Unlawful Detainer Attorney Attorney Dana Marigold represents</p></div>
  </div>
</section>

<section class="welcome">
  <div class="abs portrait" role="img" aria-label="Portrait photo of the attorney"></div>
  <h2 class="abs welcome-title">Welcome to <span>Marigold Law P.C</span></h2>
  <p class="abs welcome-text">Find the big firm style legal counsel you can work with in your hometown region at Marigold Law P.C., in Riverton, CA. Attorney Dana L. Marigold, Esq., offers a boutique law firm opportunity for clients who want to enjoy all the advantages of her broad legal experience and education.</p>
  <a class="abs btn-red" href="#">Read More</a>
</section>

<section class="abs reviews" role="img" aria-label="Dim photo of a judge's gavel and scales of justice">
  <h2 class="abs section-title">What Our Client Say</h2>
  <div class="abs quote-mark"><svg width="28" height="22" viewBox="0 0 28 22"><path fill="#bbbbbb" d="M0 22V12C0 5 4 1 11 0l1 3c-4 1-6 3-6 7h5v12zm16 0V12c0-7 4-11 11-12l1 3c-4 1-6 3-6 7h5v12z"/></svg></div>
  <p class="abs review-text">Marigold Law is our go-to source for professional and sound legal advice.&nbsp; Marigold Law has become a vital component to the success of our business as well as the businesses of the clients we have referred to Marigold Law.</p>
  <div class="abs review-tag">A Vital Component</div>
  <div class="abs review-author">Oak Ridge Accounting Partners</div>
  <div class="abs dots"><i class="on"></i><i></i><i></i></div>
</section>

<section class="news">
  <h2 class="abs section-title news-title">Latest <span>News</span></h2>
  <article class="abs post" style="left:77px">
    <div class="post-image" role="img" aria-label="Office team meeting around a table" style="background:linear-gradient(135deg,#e7eef2,#9aa9b3 60%,#4b5a66)"></div>
    <h4>Lorem Ipsum is simply dummy text</h4><time>03 August 2016</time>
    <p>Lorem Ipsum is simply dummy text of the printing and type setting industry.</p>
  </article>
  <article class="abs post" style="left:348px">
    <div class="post-image" role="img" aria-label="Lawyers consulting with a client" style="background:linear-gradient(135deg,#d9d4cc,#8c8577 55%,#2f2c28)"></div>
    <h4>Lorem Ipsum is simply dummy text</h4><time>03 August 2016</time>
    <p>Lorem Ipsum is simply dummy text of the printing and type setting industry.</p>
  </article>
  <article class="abs post" style="left:619px">
    <div class="post-image" role="img" aria-label="Gavel and scales on a desk" style="background:linear-gradient(135deg,#2a1a10,#9b6a32 55%,#d9a64f)"></div>
    <h4>Lorem Ipsum is simply dummy text</h4><time>03 August 2016</time>
    <p>Lorem Ipsum is simply dummy text of the printing and type setting industry.</p>
  </article>
  <article class="abs post" style="left:888px">
    <div class="post-image" role="img" aria-label="Glass office building facade" style="background:linear-gradient(135deg,#eef3f7,#8fa6bb 55%,#3d5870)"></div>
    <h4>Lorem Ipsum is simply dummy text</h4><time>03 August 2016</time>
    <p>Lorem Ipsum is simply dummy text of the printing and type setting industry.</p>
  </article>
</section>

<section class="abs ratings">
  <svg class="abs" style="left:0;top:0" width="370" height="145"><polygon points="0,0 330,0 370,72 330,145 0,145" fill="#ec1f27"/></svg>
  <div class="abs ratings-label" style="background:none">Rating &amp;<br>Reviews</div>
  <div class="abs badge" style="left:330px;top:40px;width:190px;height:62px;border-radius:6px"></div>
  <div class="abs badge" style="left:580px;top:25px;width:94px;height:94px;border-radius:50%"></div>
  <div class="abs badge" style="left:735px;top:47px;width:275px;height:50px;border-radius:6px"></div>
</section>

<footer class="abs footer">
  <nav class="abs footer-nav"><a href="#">Home</a><a href="#">Our Attorney</a><a href="#">Practice Areas</a><a href="#">Client Reviews</a><a href="#">News</a><a href="#">Contact</a><a href="#">Disclaimer</a></nav>
  <div class="abs social"><i></i><i></i><i></i></div>

  <div class="abs contact-item" style="left:79px">
    <span class="contact-icon"><svg width="22" height="22" viewBox="0 0 24 24"><path fill="#ec1f27" d="M12 2a7 7 0 0 0-7 7c0 5 7 13 7 13s7-8 7-13a7 7 0 0 0-7-7zm0 9.5A2.5 2.5 0 1 1 12 6.5a2.5 2.5 0 0 1 0 5z"/></svg></span>
    <div>48 Orchard Avenue,<br>Suite 210 Riverton, CA 95000<br><a href="#">VIEW MAP</a></div>
  </div>
  <div class="abs contact-item" style="left:348px">
    <span class="contact-icon"><svg width="22" height="22" viewBox="0 0 24 24"><path fill="#ec1f27" d="M6.6 10.8a15.2 15.2 0 0 0 6.6 6.6l2.2-2.2c.3-.3.7-.4 1-.2 1.1.4 2.3.6 3.6.6.6 0 1 .4 1 1V20c0 .6-.4 1-1 1A17 17 0 0 1 3 4c0-.6.4-1 1-1h3.5c.6 0 1 .4 1 1 0 1.3.2 2.5.6 3.6.1.3 0 .7-.2 1z"/></svg></span>
    <div style="padding-top:11px;font-weight:700">(555) 014-2870</div>
  </div>
  <div class="abs contact-item" style="left:619px">
    <span class="contact-icon"><svg width="22" height="22" viewBox="0 0 24 24"><rect x="4" y="9" width="16" height="11" fill="#ec1f27"/><rect x="7" y="3" width="10" height="6" fill="none" stroke="#ec1f27" stroke-width="2"/></svg></span>
    <div style="padding-top:11px">(555) 019-3304</div>
  </div>
  <div class="abs contact-item" style="left:888px">
    <span class="contact-icon"><svg width="22" height="22" viewBox="0 0 24 24"><rect x="3" y="5" width="18" height="14" fill="none" stroke="#ec1f27" stroke-width="2"/><path d="M3 6l9 7 9-7" fill="none" stroke="#ec1f27" stroke-width="2"/></svg></span>
    <div>info@marigoldlawgroup.<br>com</div>
  </div>
</footer>

<div class="abs legal">© <strong>MARIGOLD LAW P.C</strong> - 2016. All Rights Reserved.</div>

</body>
</html>
```